New Business Card Design Project

Need a design that will create an impact / strong impression towards our clients for our business. We are in the lighting business and we do lighting retrofits for large commercial to industrial clientele.

Target Market(s)

Lighting Industry

Industry/Entity Type

Business

Font styles to use
Other font styles liked:
• we would like to use the font on our logo, not sure what it is though..

Requirements
Must have
• Our logo.
Nice to have
• We are open to suggestions that have to do with lighting.

```html
<!DOCTYPE html>
<html lang="en">
<head>
<meta charset="utf-8">
<title>Kestrel Lighting Group – Business Card</title>
<link href="https://fonts.googleapis.com/css2?family=Mulish:wght@400;600&family=Open+Sans:wght@400;600;700&display=swap" rel="stylesheet">
<style>
  :root {
    --backdrop: #2b2b2b;
    --card-white: #ffffff;
    --card-green: #0b8236;
    --brand-dark: #163a12;
    --brand-mid: #2f7d32;
    --text-grey: #555555;
    --text-white: #ffffff;
  }
  * { margin: 0; padding: 0; box-sizing: border-box; }
  html, body { width: 1200px; height: 960px; overflow: hidden; }
  body {
    background: var(--backdrop);
    font-family: "Open Sans", Arial, sans-serif;
    position: relative;
  }
  .card {
    position: absolute;
    width: 600px;
    height: 343px;
    box-shadow: 0 3px 8px rgba(0,0,0,0.45);
    overflow: hidden;
  }
  .card--front { left: 314px; top: 113px; background: var(--card-white); }
  .card--back { left: 311px; top: 472px; background: var(--card-green); color: var(--text-white); }

  /* brand lockup */
  .brand { position: absolute; display: flex; flex-direction: column; }
  .brand__row { display: flex; align-items: flex-end; gap: 10px; }
  .brand__name { font-weight: 700; line-height: 1; letter-spacing: 1px; }
  .brand__mark { display: block; }
  .brand__legal { font-weight: 600; text-transform: uppercase; white-space: nowrap; }

  .card--front .brand { left: 27px; top: 32px; }
  .card--front .brand__name { font-size: 44px; color: var(--brand-dark); letter-spacing: 2px; }
  .card--front .brand__mark { width: 16px; height: 16px; background: var(--brand-mid); margin-bottom: 6px; }
  .card--front .brand__legal {
    font-size: 11px; letter-spacing: 1.1px; color: var(--brand-dark);
    margin-top: 6px; border-top: 1px solid var(--brand-dark); padding-top: 3px;
  }

  .card--back .brand { left: 0; right: 0; top: 124px; align-items: center; }
  .card--back .brand__name { font-size: 58px; color: var(--text-white); letter-spacing: 2px; }
  .card--back .brand__mark { width: 22px; height: 22px; background: var(--text-white); margin-bottom: 8px; }
  .card--back .brand__legal {
    font-size: 13px; letter-spacing: 1.6px; margin-top: 8px;
    border-top: 1.5px solid var(--text-white); padding-top: 4px;
  }

  /* address & contacts */
  .address {
    position: absolute; left: 27px; top: 151px;
    font-family: "Mulish", Arial, sans-serif;
    font-size: 16px; line-height: 19.5px; color: var(--text-grey); font-style: normal;
  }
  .contacts {
    position: absolute; left: 28px; top: 218px; list-style: none;
    font-family: "Mulish", Arial, sans-serif;
    font-size: 16px; line-height: 19.2px; color: var(--text-grey);
  }
  .contacts li { display: flex; align-items: center; gap: 9px; }
  .contacts svg { width: 13px; height: 13px; fill: var(--brand-dark); flex: none; }

  /* name band */
  .name-band { position: absolute; right: 0; top: 218px; width: 236px; height: 58px; }
  .name-band svg { position: absolute; inset: 0; }
  .name-band__text { position: absolute; right: 26px; top: 4px; text-align: right; color: var(--text-white); }
  .name-band__name { font-size: 19px; font-weight: 700; line-height: 24px; }
  .name-band__role { font-family: "Mulish", Arial, sans-serif; font-size: 16px; line-height: 22px; letter-spacing: 0.5px; }

  .website {
    position: absolute; left: 0; right: 0; top: 280px; text-align: center;
    font-size: 15px; letter-spacing: 3.2px;
  }
</style>
</head>
<body>
  <section class="card card--front" aria-label="Business card front">
    <div class="brand">
      <div class="brand__row">
        <span class="brand__name">KESTREL</span>
        <span class="brand__mark" aria-hidden="true"></span>
      </div>
      <span class="brand__legal">Kestrel Lighting Group, LLC.</span>
    </div>

    <address class="address">2210 Birchwood Court<br>Fairbanks<br>Alaska 99712</address>

    <ul class="contacts">
      <li><svg viewBox="0 0 16 16" aria-label="Phone"><path d="M1 6c0-3 14-3 14 0v2h-4V6.5H5V8H1zM3 9h10l1 6H2z"/></svg>907 555 0182</li>
      <li><svg viewBox="0 0 16 16" aria-label="Mobile"><path d="M4 0h8v16H4zM5.5 1.5v11h5v-11z"/></svg>907 555 0247</li>
      <li><svg viewBox="0 0 16 16" aria-label="Fax"><path d="M4 1h8v4H4zM1 6h14v6h-2V9H3v3H1zM4 10h8v5H4z"/></svg>907 555 0316</li>
      <li><svg viewBox="0 0 16 16" aria-label="Email"><path d="M1 3h14v1.5L8 9 1 4.5zM1 6.5l7 4.5 7-4.5V13H1z"/></svg>mark@kestrelgroup.com</li>
      <li><svg viewBox="0 0 16 16" aria-label="Website"><circle cx="8" cy="8" r="7"/></svg>www.kestrelgroup.com</li>
    </ul>

    <div class="name-band">
      <svg viewBox="0 0 236 58" preserveAspectRatio="none" aria-hidden="true"><polygon points="56,0 236,0 236,58 0,58" fill="var(--brand-dark)"/></svg>
      <div class="name-band__text">
        <div class="name-band__name">MARK ELLISON</div>
        <div class="name-band__role">CEO/FOUNDER</div>
      </div>
    </div>
  </section>

  <section class="card card--back" aria-label="Business card back">
    <div class="brand">
      <div class="brand__row">
        <span class="brand__name">KESTREL</span>
        <span class="brand__mark" aria-hidden="true"></span>
      </div>
      <span class="brand__legal">Kestrel Lighting Group, LLC.</span>
    </div>
    <div class="website">www.kestrellightinggroup.com</div>
  </section>
</body>
</html>
```